Norvane Website Design (New Start Up Investment Management Firm)

We need a website designed. We have attached a Powerpoint with our proposed website content (which is quite minimal), the format is just a suggestion but we would like to see your alternative and improved ideas. We are a boutique investment firm so are looking for something sleek and professional. I have included on the last page of the attachment our brand colours and font styles as well as attaching our logo design. We would like the successful designer to design the website and build the buttons etc.

On the "Contact Us" page, we are open to suggestions on how best to show the map, whether is should be static or open a google maps page. We would like the phone number and email address to be set up so people can click on them on their phone and it calls us or emails us directly.

We would prefer not to have photos of landscapes on the site.
Our website is hosted on a Linux based website.

We would also like 3 links at the bottom of each page for links to pdfs:
- Disclaimer, Terms and Conditions of Web Site Use
- Stewardship
- Pillar III

Target Market(s)

Institutional Investors

Industry/Entity Type

Investment

Coding

Coded - Design and coding required

Number of Pages Required

3 page

Font styles to use
Other font styles liked:
• Logo: Lato, Text: Source Sans Pro

Colors

Designer to choose colors to be used in the design.

Requirements
Must have
• The website must use the colours and fonts on the last page of the attached powerpoint. I can't see an option to select the exact colour palette below so please look at the PPT.
• For others please see Project description.
Should not have
• Landscape photos

```html
<!DOCTYPE html>
<html lang="en">
<head>
<meta charset="utf-8">
<title>Norvane Investment Management</title>
<link rel="stylesheet" href="https://fonts.googleapis.com/css2?family=Lato:wght@400;700;900&display=swap">
<style>
:root{
  --navy:#0c2c5f;
  --ink:#3b3b3b;
  --muted:#555;
  --band:#ebebeb;
  --panel:#f1f1f1;
  --tab-dark:#4a4a4a;
  --sky:#4ba8e0;
  --white:#fff;
  --social-one:#3b5a9a;
  --social-two:#1da1f2;
  --social-three:#e9553f;
}
*{box-sizing:border-box;margin:0;padding:0}
html,body{width:952px;height:1200px;overflow:hidden;background:var(--white)}
body{position:relative;font-family:'Lato',sans-serif;color:var(--ink)}
.abs{position:absolute}

/* header */
.brand{left:104px;top:25px;display:flex;align-items:center;gap:12px}
.brand-mark{width:44px;height:44px;background:var(--navy)}
.brand-name{font-size:34px;font-weight:700;color:var(--navy);letter-spacing:1px;line-height:1}
.brand-sub{font-size:8px;font-weight:700;color:var(--navy);letter-spacing:2px;margin-top:3px}
.call{left:568px;top:21px;display:flex;align-items:center;gap:8px}
.call-icon{width:21px;height:21px;border-radius:50%;background:var(--navy);display:flex;align-items:center;justify-content:center}
.call-label{font-size:9px;color:var(--ink)}
.call-number{font-size:13px;color:var(--navy);margin-left:2px}
.search{left:750px;top:16px;width:99px;height:26px;border:1px solid #bbb;display:flex;align-items:center;padding-left:9px;gap:7px;font-size:7px;color:#777}
.nav{left:425px;top:65px;display:flex;align-items:center;font-size:9.5px;color:var(--navy)}
.nav a{color:inherit;text-decoration:none;display:block;padding:5px 10px}
.nav .active{background:var(--navy);color:var(--white)}
.nav a+a{margin-left:12px}

/* intro band */
.band{left:0;top:100px;width:952px;height:334px;background:var(--band)}
.tab{top:149px;width:206px;height:35px;display:flex;align-items:center;justify-content:center;gap:10px;font-size:10px;font-weight:700;color:var(--white)}
.tab-about{left:159px;background:var(--navy)}
.tab-approach{left:372px;background:var(--tab-dark);font-weight:400}
.tab-contact{left:586px;background:var(--tab-dark);font-weight:400}
.tab-square{width:18px;height:18px;background:var(--white)}
.intro-card{left:159px;top:192px;width:634px;height:193px;background:var(--white);box-shadow:0 1px 3px rgba(0,0,0,.12);padding:28px 58px 0 43px}
.intro-lead{font-size:11.5px;line-height:19px;color:var(--navy);margin-bottom:15px}
.intro-body{font-size:11.5px;line-height:19px;color:var(--muted)}

/* services */
.section-title{left:0;width:952px;top:481px;text-align:center;font-size:20px;font-weight:700;color:var(--navy)}
.section-rule{left:448px;top:525px;width:57px;height:2px;background:#aaa}
.service{top:570px;width:140px;text-align:center;font-size:12px;color:var(--ink)}
.service svg{display:block;margin:0 auto 18px;width:48px;height:48px;fill:var(--navy)}

/* investment panel */
.invest{left:103px;top:710px;width:445px;height:321px;background:var(--panel);padding:38px 50px 0 40px;overflow:hidden}
.invest-art{position:absolute;left:240px;top:80px;width:205px;height:241px;background:radial-gradient(ellipse at 60% 50%,#e3e3e3,rgba(241,241,241,0) 70%)}
.invest h2{position:relative;font-size:19px;font-weight:700;color:var(--navy);margin-bottom:22px}
.invest-lead{position:relative;font-size:12px;line-height:19px;color:var(--ink);margin-bottom:18px}
.invest-body{position:relative;font-size:10px;line-height:19px;color:var(--muted)}
.btn{display:inline-block;background:var(--navy);color:var(--white);font-size:10.5px;font-weight:700;padding:10px 20px}
.invest .btn{position:absolute;left:46px;top:243px}

/* news */
.news{left:572px;top:708px;width:276px;height:323px;background:var(--navy);color:var(--white);padding:25px 25px 0 25px}
.news h2{font-size:19px;font-weight:700;margin-bottom:26px}
.news-item{display:flex;gap:17px;padding-left:4px}
.news-item+.news-item{margin-top:16px;padding-top:17px;border-top:1px solid #2a4777;margin-left:41px;padding-left:0}
.news-item+.news-item .arrow{margin-left:-37px}
.arrow{flex:none;width:20px;height:20px;background:#6c6c6c;display:flex;align-items:center;justify-content:center;margin-top:2px}
.news-title{font-size:11.5px;line-height:15px;margin-bottom:9px}
.news-text{font-size:8px;line-height:13px}
.news .btn-sky{position:absolute;left:176px;top:284px;background:var(--sky);color:var(--navy);font-size:8.5px;font-weight:700;padding:7px 9px}

/* footer */
.footer{left:0;top:1087px;width:952px;height:113px;background:var(--panel)}
.foot-brand{left:106px;top:1124px;display:flex;align-items:center;gap:9px}
.foot-brand .brand-mark{width:36px;height:36px}
.foot-brand .brand-name{font-size:27px}
.foot-brand .brand-sub{font-size:6.5px;letter-spacing:1.6px}
.follow{left:350px;top:1129px;display:flex;align-items:center;gap:6px;font-size:8px;color:var(--ink)}
.follow span{margin-right:10px}
.social{width:24px;height:24px;border-radius:50%}
.social-one{background:var(--social-one)}.social-two{background:var(--social-two)}.social-three{background:var(--social-three)}
.legal{left:603px;top:1126px;font-size:8.5px;color:var(--ink)}
.legal p+p{margin-top:13px}
</style>
</head>
<body>

<header>
  <div class="abs brand">
    <div class="brand-mark"></div>
    <div>
      <div class="brand-name">NORVANE</div>
      <div class="brand-sub">INVESTMENT MANAGEMENT</div>
    </div>
  </div>
  <div class="abs call">
    <div class="call-icon"><svg width="11" height="11" viewBox="0 0 24 24" fill="#fff"><path d="M6.6 10.8a15 15 0 006.6 6.6l2.2-2.2c.3-.3.7-.4 1-.2 1.1.4 2.3.6 3.6.6.6 0 1 .4 1 1V20c0 .6-.4 1-1 1A17 17 0 013 4c0-.6.4-1 1-1h3.5c.6 0 1 .4 1 1 0 1.3.2 2.5.6 3.6.1.3 0 .7-.2 1z"/></svg></div>
    <span class="call-label">CALL US</span>
    <span class="call-number">(555).014.2290</span>
  </div>
  <div class="abs search">
    <svg width="8" height="8" viewBox="0 0 10 10" fill="none" stroke="#666" stroke-width="1.5"><circle cx="4" cy="4" r="3"/><path d="M6.3 6.3L9 9"/></svg>
    SEARCH
  </div>
  <nav class="abs nav">
    <a class="active">HOME</a><a>ABOUT US</a><a>SERVICES</a><a>INVESTMENT</a><a>BLOG</a><a>CONTACT US</a>
  </nav>
</header>

<section>
  <div class="abs band"></div>
  <div class="abs tab tab-about"><span class="tab-square"></span>ABOUT NORVANE</div>
  <div class="abs tab tab-approach">
    <svg width="14" height="12" viewBox="0 0 14 12" fill="#fff"><ellipse cx="6" cy="5" rx="6" ry="4.2"/><path d="M2 8l-1 3 4-2z"/></svg>
    OUR APPROACH AND PHILOSOPHY</div>
  <div class="abs tab tab-contact">
    <svg width="14" height="11" viewBox="0 0 14 11" fill="#fff"><rect width="14" height="11" rx="1"/><path d="M0 1l7 5 7-5" stroke="#4a4a4a" stroke-width="1.3" fill="none"/></svg>
    CONTACT US</div>
  <div class="abs intro-card">
    <p class="intro-lead">Norvane Investment Management was founded in 2016 with a clear vision to create an independent and nimble firm focused on generating superior risk-adjusted returns.</p>
    <p class="intro-body">Norvane has designed an innovative investment approach which aims to harness the best elements of alternative investment management whilst reducing its recognised shortcomings. We are a performance and client focused firm, committed to building lasting relationships, treating our clients like partners rather than revenue streams.</p>
  </div>
</section>

<section>
  <h2 class="abs section-title">OUR SERVICES</h2>
  <div class="abs section-rule"></div>

  <div class="abs service" style="left:84px">
    <svg viewBox="0 0 48 48"><path d="M24 6L6 15v3h36v-3z"/><rect x="8" y="20" width="5" height="16"/><rect x="16" y="20" width="5" height="16"/><rect x="27" y="20" width="5" height="16"/><rect x="35" y="20" width="5" height="16"/><rect x="6" y="38" width="36" height="4"/></svg>
    Capital Syndication</div>
  <div class="abs service" style="left:219px">
    <svg viewBox="0 0 48 48"><circle cx="24" cy="15" r="9"/><path d="M8 44c0-10 7-15 16-15s16 5 16 15z"/></svg>
    Advisory</div>
  <div class="abs service" style="left:353px">
    <svg viewBox="0 0 48 48"><circle cx="24" cy="24" r="17" fill="none" stroke="#0c2c5f" stroke-width="3"/><circle cx="24" cy="24" r="10"/><text x="24" y="29" text-anchor="middle" font-size="14" font-weight="700" fill="#fff" font-family="Lato,sans-serif">$</text><path d="M38 8l2 8-8-1z"/><path d="M10 40l-2-8 8 1z"/></svg>
    Investments</div>
  <div class="abs service" style="left:491px">
    <svg viewBox="0 0 48 48"><path d="M4 18l10-6 8 4 6-3 16 6-4 10-10 8-8-5-12-3z" fill="none" stroke="#0c2c5f" stroke-width="3" stroke-linejoin="round"/><path d="M20 26l6 4m-2-8l8 6" stroke="#0c2c5f" stroke-width="2.5"/></svg>
    Joint Ventures</div>
  <div class="abs service" style="left:622px">
    <svg viewBox="0 0 48 48"><circle cx="17" cy="30" r="9" fill="none" stroke="#0c2c5f" stroke-width="6" stroke-dasharray="3 2.5"/><circle cx="17" cy="30" r="5"/><circle cx="33" cy="15" r="7" fill="none" stroke="#0c2c5f" stroke-width="5" stroke-dasharray="3 2.5"/><circle cx="33" cy="15" r="4"/></svg>
    Solutions</div>
  <div class="abs service" style="left:745px">
    <svg viewBox="0 0 48 48"><circle cx="24" cy="6" r="4"/><rect x="19" y="11" width="10" height="8" rx="2"/><path d="M24 19v5M9 24h30M9 24v5M24 24v5M39 24v5" stroke="#0c2c5f" stroke-width="2" fill="none"/><circle cx="9" cy="33" r="3.5"/><circle cx="24" cy="33" r="3.5"/><circle cx="39" cy="33" r="3.5"/><rect x="4" y="37" width="10" height="7" rx="2"/><rect x="19" y="37" width="10" height="7" rx="2"/><rect x="34" y="37" width="10" height="7" rx="2"/></svg>
    Management</div>
</section>

<section class="abs invest">
  <div class="invest-art" role="img" aria-label="Faint background illustration of a savings jar with a coin"></div>
  <h2>INVESTMENT MANAGEMENT</h2>
  <p class="invest-lead">But I must explain to you how all this mistaken idea of denouncing pleasure and praising pain was born and.</p>
  <p class="invest-body">At vero eos et accusamus et iusto odio dignissimos ducimus qui blanditiis praesentium voluptatum deleniti atque corrupti quos dolores et quas molestias excepturi sint occaecati cupiditate non provident, similique sunt in culpa qui officia deserunt mollitia animi, id est laborum et dolorum fuga.</p>
  <a class="btn">READ MORE</a>
</section>

<aside class="abs news">
  <h2>LATEST NEWS</h2>
  <div class="news-item">
    <div class="arrow"><svg width="6" height="8" viewBox="0 0 6 8" fill="none" stroke="#fff" stroke-width="1.4"><path d="M1 1l3 3-3 3"/></svg></div>
    <div>
      <p class="news-title">Sed ut perspiciatis unde omnis iste natus error sit.</p>
      <p class="news-text">qui dolorem ipsum quia dolor sit amet, consec tetur, adipisci velit, sed quia non numquam eius modi tempora.</p>
    </div>
  </div>
  <div class="news-item">
    <div class="arrow"><svg width="6" height="8" viewBox="0 0 6 8" fill="none" stroke="#fff" stroke-width="1.4"><path d="M1 1l3 3-3 3"/></svg></div>
    <div>
      <p class="news-title">Sed ut perspiciatis unde omnis iste natus error sit.</p>
      <p class="news-text">qui dolorem ipsum quia dolor sit amet, consec tetur, adipisci velit, sed quia non numquam eius modi tempora.</p>
    </div>
  </div>
  <a class="btn-sky">READ ALL NEWS</a>
</aside>

<footer>
  <div class="abs footer"></div>
  <div class="abs brand foot-brand">
    <div class="brand-mark"></div>
    <div>
      <div class="brand-name">NORVANE</div>
      <div class="brand-sub">INVESTMENT MANAGEMENT</div>
    </div>
  </div>
  <div class="abs follow">
    <span>FOLLOW US ON</span>
    <a class="social social-one" aria-label="Social profile one"></a>
    <a class="social social-two" aria-label="Social profile two"></a>
    <a class="social social-three" aria-label="Social profile three"></a>
  </div>
  <div class="abs legal">
    <p>Disclaimer &nbsp;|&nbsp; Terms and Conditions &nbsp;|&nbsp; Stewardship &nbsp;|&nbsp; Pillar III</p>
    <p>Copyrights @ 2017 All Rights Reserved</p>
  </div>
</footer>

</body>
</html>
```